BrindleStaffing Business Card Design

We are a staffing company finding positions for dedicated nurses and physicians.

Target Market(s)

Business Professionals

Industry/Entity Type

Staffing

Contact Information for Business Card

Gordon Pratley
Chairman
417 39th Avenue South
SAINT PETERSBURG FL 33712
813-555-4172 Mobile
813-555-8036 Fax
gpratley@brindlestaffing.com
www.brindlestaffing.com

Font styles to use
Sans Serif

Colors
fbee3e
f04a50
f37122

Requirements
Must have
• Logo Attached, see colors below. We'd like to see Yellow, Orange and Red.

```html
<!DOCTYPE html>
<html lang="en">
<head>
<meta charset="utf-8">
<title>BrindleStaffing Business Card</title>
<link rel="stylesheet" href="https://fonts.googleapis.com/css2?family=Lato:wght@400;700&display=swap">
<style>
  :root {
    --backdrop: #5b5b5b;
    --card-white: #ffffff;
    --brand-yellow: #fbee3e;
    --brand-orange: #f37122;
    --brand-red: #f04a50;
    --ink: #2a2a2a;
  }
  * { margin: 0; padding: 0; box-sizing: border-box; }
  html, body { width: 1200px; height: 802px; overflow: hidden; }
  body {
    background: var(--backdrop);
    position: relative;
    font-family: 'Lato', sans-serif;
  }
  .card {
    position: absolute;
    top: 274px;
    width: 443px;
    height: 265px;
    box-shadow: 2px 3px 6px rgba(0,0,0,0.45);
  }
  .card-front { left: 136px; background: var(--card-white); }
  .card-back {
    left: 624px;
    background: linear-gradient(to bottom, var(--brand-yellow) 0%, var(--brand-orange) 45%, var(--brand-red) 100%);
  }
  .wordmark {
    position: absolute;
    font-family: 'Lato', sans-serif;
    font-weight: 700;
    white-space: nowrap;
    letter-spacing: -0.3px;
  }
  .card-front .wordmark {
    left: 27px;
    top: 120px;
    font-size: 25px;
    color: var(--brand-orange);
  }
  .card-back .wordmark {
    left: 0; right: 0;
    top: 112px;
    text-align: center;
    font-size: 32px;
    color: #ffffff;
  }
  .divider {
    position: absolute;
    left: 222px;
    top: 56px;
    width: 1px;
    height: 154px;
    background: linear-gradient(to bottom, var(--brand-orange), var(--brand-red));
  }
  .contact { position: absolute; left: 235px; top: 58px; color: var(--ink); }
  .contact-name {
    font-size: 19px;
    font-weight: 400;
    line-height: 23px;
    letter-spacing: 0.2px;
  }
  .contact-name .first { color: var(--brand-orange); }
  .contact-name .last { color: var(--brand-red); }
  .contact-title {
    font-size: 12px;
    line-height: 15px;
    color: var(--ink);
    margin-bottom: 6px;
  }
  .contact-line {
    display: flex;
    align-items: center;
    gap: 4px;
    font-size: 12.5px;
    line-height: 16px;
    white-space: nowrap;
  }
  .contact-line svg { width: 10px; height: 10px; flex: none; }
  .address { margin-top: 8px; font-size: 12.5px; line-height: 16px; white-space: nowrap; }
</style>
</head>
<body>
  <section class="card card-front" aria-label="Business card front">
    <div class="wordmark">BrindleStaffing</div>
    <div class="divider"></div>
    <div class="contact">
      <h1 class="contact-name"><span class="first">Gordon</span> <span class="last">Pratley</span></h1>
      <p class="contact-title">Chairman</p>
      <div class="contact-line">
        <svg viewBox="0 0 10 10" aria-hidden="true"><path fill="#f37122" d="M1 3.5c0-1.5 1.8-2 4-2s4 .5 4 2v1H7V3.5H3v1H1z M2.5 5h5l1 4h-7z"/></svg>
        <span>813-555-4172 Mobile</span>
      </div>
      <div class="contact-line">
        <svg viewBox="0 0 10 10" aria-hidden="true"><rect x="1" y="4" width="8" height="5" fill="#f37122"/><rect x="2.5" y="1" width="5" height="3.5" fill="none" stroke="#f37122" stroke-width="0.9"/></svg>
        <span>813-555-8036 Fax</span>
      </div>
      <div class="contact-line">
        <svg viewBox="0 0 10 10" aria-hidden="true"><rect x="0.5" y="2" width="9" height="6.5" fill="#f37122"/><path d="M0.8 2.3L5 5.8 9.2 2.3" stroke="#fff" stroke-width="0.9" fill="none"/></svg>
        <span>gpratley@brindlestaffing.com</span>
      </div>
      <div class="contact-line">
        <svg viewBox="0 0 10 10" aria-hidden="true"><circle cx="5" cy="5" r="4.5" fill="#f37122"/><path d="M3 3.5c1 .2 1.5 1 1 2s.5 2 1.5 2.5M6 2c.5.8 2 1 2.3 2" stroke="#fff" stroke-width="0.9" fill="none"/></svg>
        <span>www.brindlestaffing.com</span>
      </div>
      <p class="address">417 39th Avenue South<br>SAINT PETERSBURG FL 33712</p>
    </div>
  </section>
  <section class="card card-back" aria-label="Business card back">
    <div class="wordmark">BrindleStaffing</div>
  </section>
</body>
</html>
```